SkyvornQ Business Cards and Stationary Design

Need a design for our business cards and stationary. I want to carry on the theme of the logo. I want the business cards to have a design on the back. I would like the business cards and the stationary to carry the same theme, design scheme, and branding

Target Market(s)

Airlines and Maintenance Facilities

Industry/Entity Type

Aviation

Contact Information for Business Card

Name
Position Title
Address: 4827 Trellis Hollow Road, Fort Pierce, Florida, 34951
Office Number
Mobile Number
Email
Website

Font styles to use
Serif
Sans Serif

Colors

Designer to choose colors to be used in the design.

```html
<!DOCTYPE html>
<html lang="en">
<head>
<meta charset="utf-8">
<title>SkyvornQ Business Card</title>
<link href="https://fonts.googleapis.com/css2?family=Montserrat:wght@400;500;600;700;800&display=swap" rel="stylesheet">
<style>
  :root {
    --backdrop: #1e1e1f;
    --paper: #ffffff;
    --accent: #1e9ad8;
    --ink: #14264a;
    --navy-light: #1c4a86;
    --navy-dark: #133d76;
    --white: #ffffff;
  }
  * { margin: 0; padding: 0; box-sizing: border-box; }
  html, body {
    width: 1200px; height: 897px; overflow: hidden;
    background: var(--backdrop);
    font-family: "Montserrat", sans-serif;
  }
  .card {
    position: absolute; left: 347px; width: 499px; height: 284px;
  }
  .card-front { top: 158px; background: var(--paper); color: var(--ink); }
  .card-back {
    top: 465px;
    background: linear-gradient(200deg, var(--navy-light) 0%, var(--navy-dark) 45%, var(--navy-dark) 100%);
  }
  .holder-name {
    position: absolute; left: 23px; top: 36px;
    font-size: 21px; font-weight: 500; color: var(--accent); line-height: 1;
  }
  .holder-title {
    position: absolute; left: 23px; top: 63px;
    font-size: 13px; font-weight: 500; line-height: 1;
  }
  .title-rule {
    position: absolute; left: 23px; top: 80px; width: 19px; height: 1px; background: var(--accent);
  }
  .contact-list {
    position: absolute; left: 23px; top: 110px; list-style: none;
    font-size: 13px; font-weight: 500; line-height: 16.3px;
  }
  .contact-list .label { color: var(--accent); font-weight: 400; }
  .address {
    position: absolute; left: 23px; top: 207px;
    font-size: 13px; font-weight: 500; line-height: 16px; font-style: normal;
  }
  .brand-front {
    position: absolute; left: 300px; top: 30px; width: 176px; text-align: center;
  }
  .brand-front svg { display: block; margin: 0 auto; }
  .brand-front .wordmark {
    margin-top: 10px; font-size: 21px; font-weight: 800; letter-spacing: 3px; color: var(--ink);
  }
  .back-pattern { position: absolute; inset: 0; }
  .brand-back {
    position: absolute; left: 0; right: 0; top: 50px; text-align: center; color: var(--white);
  }
  .brand-back svg { display: block; margin: 0 auto; }
  .brand-back .wordmark {
    margin-top: 16px; font-size: 34px; font-weight: 800; letter-spacing: 6px; padding-left: 6px;
  }
  .back-url {
    position: absolute; left: 0; right: 0; top: 233px; text-align: center;
    color: var(--white); font-size: 14.5px; font-weight: 600;
  }
</style>
</head>
<body>
  <section class="card card-front">
    <h1 class="holder-name">Dorian Felcamp</h1>
    <p class="holder-title">Co-Owner</p>
    <div class="title-rule"></div>
    <ul class="contact-list">
      <li><span class="label">M:</span> (555) 318-4702</li>
      <li><span class="label">T:</span> 555-207-6641</li>
      <li><span class="label">E:</span> info@skyvornq.com</li>
      <li><span class="label">W:</span> www.skyvornq.com</li>
    </ul>
    <address class="address">4827 Trellis Hollow Road,<br>Fort Pierce,<br>Florida, 34951</address>
    <div class="brand-front">
      <svg width="58" height="58" viewBox="0 0 58 58" aria-hidden="true">
        <circle cx="29" cy="29" r="26" fill="none" stroke="var(--ink)" stroke-width="5"/>
      </svg>
      <div class="wordmark">SKYVORNQ</div>
    </div>
  </section>

  <section class="card card-back">
    <div class="back-pattern" role="img" aria-label="Faint repeating brand symbol pattern across the card back"></div>
    <div class="brand-back">
      <svg width="90" height="90" viewBox="0 0 90 90" aria-hidden="true">
        <circle cx="45" cy="45" r="40" fill="none" stroke="var(--white)" stroke-width="7"/>
      </svg>
      <div class="wordmark">SKYVORNQ</div>
    </div>
    <p class="back-url">www.skyvornq.com</p>
  </section>
</body>
</html>
```